Labelling for Ice cream products for Tandle k's company

Hi
We are an Ice cream/Gelato company based in Birmingham UK. We need a design for packaging for some of our products. We are in need of packaging for round 400-500ml tubs and smaller round 125ml tubs (with lids). We also need a design for our plastic Ice Lolly wrappers (will provide dimensions if needed) this will be for a roll that is used on an Ice lolly wrapping machine, and also designs for stickers that will go on the top of 10 litre tubs and rectangular stickers for the side of 5 litre napoli pans. We currently have a diner that we sell, so a simple design for our inhouse scoop cups would also be good. The designs should be editable and allow for incorporation of pictures of different flavours. I will attach our logo, as we would like the design to be congruent with the logos colours. The design fennick orrows currently use is nice and though we want our packaging to be unique, something along those lines is were our minds are at t he moment. The designer is free to play with designs and make it look as high quality as they wish, though is must preferably look fun but not childish. A design that incorporates pascal colours would be nice but not essential so feel free to experiment.
So to conclude:
1. Design for 400-500ml round tubs with lids.
2. Design for Ice lolly wrappers.
3. Design for square labels for the top of 10 litre tubs and rectangular labes for the side of 5 litre napoli pans.
4. Basic design for in-house scoop cups.
I will upload our logo.
Many thanks and kind regards

Grant

Industry/Entity Type

Ice cream Desserts

Colors
FFC000
F8CF3A
FAE287
FDF2CF
FEFAEE
EE7325
F08F49
F5BC92
FAE3D3
FDF4ED
EB3D1F
EC4F4E
F09395
F8D3D4
FCEDEE
E54698
E96AAD
F1A4CE
F9D9EA
FCEFF6
A7469A
B969AE
D3A5CF
EDDBEB
F8F0F9

Requirements
Nice to have
• It would also be nice to have a design for swirlano wrappers

```html
<!DOCTYPE html>
<html lang="en">
<head>
<meta charset="utf-8">
<title>Tandle k's – Ice-cream Labels</title>
<link href="https://fonts.googleapis.com/css2?family=Chewy&family=Yellowtail&family=Kalam:wght@700&family=Raleway:wght@300;500&family=Oswald:wght@400&family=Montserrat:wght@800&display=swap" rel="stylesheet">
<style>
:root{
  --stage:#e4e4e4;
  --white:#ffffff;
  --blush:#f9d9ea;
  --blush-soft:#fceff6;
  --pink:#f1a4ce;
  --magenta:#e5068d;
  --magenta-deep:#b91b8f;
  --plum:#8e2a8e;
  --plum-dark:#6d1f73;
  --butter:#f8e04a;
  --cream:#efe6c4;
  --cream-shade:#d9cc9b;
}
*{margin:0;padding:0;box-sizing:border-box}
html,body{width:1039px;height:1200px;overflow:hidden;background:var(--stage)}
.board{position:relative;width:1039px;height:1200px}
.label{position:absolute;overflow:hidden;background:var(--white);box-shadow:0 3px 8px rgba(0,0,0,.28)}
.label svg.bg{position:absolute;inset:0;width:100%;height:100%}
.label>*:not(svg){position:absolute}
.brand{font-family:"Chewy","Kalam",cursive;color:var(--magenta-deep);white-space:nowrap;text-align:center;line-height:1}
.script{font-family:"Yellowtail","Kalam",cursive;color:var(--plum);white-space:nowrap;text-align:center;line-height:1}
.product{font-family:"Chewy","Kalam",cursive;color:var(--plum);white-space:nowrap;text-align:center;line-height:1;letter-spacing:1px;text-shadow:1px 2px 2px rgba(0,0,0,.25)}
.tagline{font-family:"Kalam",cursive;font-weight:700;color:var(--plum);white-space:nowrap;line-height:1}
.claim{display:flex;align-items:center;color:var(--white);white-space:nowrap}
.claim .pct{font-family:"Raleway",sans-serif;font-weight:300;line-height:.95;padding-right:4px;border-right:1px solid rgba(255,255,255,.7)}
.claim .pct b{display:block;font-weight:500}
.claim .pct small{display:block;font-weight:500;letter-spacing:.2px}
.claim .craft{font-family:"Oswald",sans-serif;line-height:1.1;padding-left:4px}
.flavour{font-family:"Montserrat",sans-serif;font-weight:800;color:var(--white);white-space:nowrap;line-height:1}
.scoop{border-radius:50% 50% 42% 42%/60% 60% 40% 40%;background:radial-gradient(ellipse at 40% 35%,#faf6e4 0%,var(--cream) 55%,var(--cream-shade) 100%);box-shadow:0 4px 6px rgba(0,0,0,.3)}
.size{border-radius:50%;background:var(--plum-dark);border:2px solid var(--white);color:var(--white);font-family:"Oswald",sans-serif;display:flex;align-items:center;justify-content:center;text-align:center;line-height:1}
</style>
</head>
<body>
<main class="board">

  <!-- Shop banner -->
  <section class="label banner" style="left:129px;top:42px;width:762px;height:476px">
    <svg class="bg" viewBox="0 0 762 476" preserveAspectRatio="none" aria-hidden="true">
      <defs>
        <linearGradient id="bannerBody" x1="0" x2="1"><stop offset="0" stop-color="#b01b91"/><stop offset="1" stop-color="#e5068d"/></linearGradient>
      </defs>
      <path d="M0 110 C10 60 40 70 50 100 C60 150 100 140 110 90 C120 50 150 40 170 60 L300 60 C320 50 330 30 360 40 L520 40 C540 30 560 40 570 80 C575 110 600 110 605 80 C610 50 650 60 660 110 C665 130 690 130 695 100 C700 60 740 40 762 50 L762 476 L0 476Z" fill="var(--blush)"/>
      <path d="M0 225 C120 240 260 250 400 230 C520 212 640 190 762 178 L762 476 L0 476Z" fill="url(#bannerBody)"/>
    </svg>
    <div class="brand" style="left:130px;top:170px;width:500px;font-size:96px">Tandle k's</div>
    <div class="script" style="left:40px;top:322px;width:270px;font-size:38px;color:var(--white)">Premium Gelato</div>
    <div class="tagline" style="left:40px;top:372px;width:270px;text-align:center;font-size:22px;color:var(--white)">Deeply Decedant</div>
    <div class="product" style="left:318px;top:322px;width:420px;font-size:82px;color:var(--butter);-webkit-text-stroke:3px var(--plum-dark)">Ice-cream</div>
  </section>

  <!-- 400ml tub label -->
  <section class="label tub" style="left:35px;top:552px;width:310px;height:319px">
    <svg class="bg" viewBox="0 0 310 319" preserveAspectRatio="none" aria-hidden="true">
      <path d="M0 45 C20 30 40 40 50 55 C60 70 75 40 100 35 L230 30 C250 25 270 45 275 60 C280 75 290 50 310 40 L310 319 L0 319Z" fill="var(--blush)"/>
      <path d="M0 240 C80 220 160 228 230 225 C260 222 290 215 310 212 L310 319 L0 319Z" fill="var(--magenta-deep)"/>
      <rect x="0" y="286" width="310" height="18" fill="var(--magenta)"/>
    </svg>
    <div class="brand" style="left:30px;top:52px;width:250px;font-size:42px">Tandle k's</div>
    <div class="script" style="left:30px;top:126px;width:250px;font-size:22px">Premium Gelato</div>
    <div class="product" style="left:25px;top:152px;width:260px;font-size:46px">Ice-cream</div>
    <div class="tagline" style="left:47px;top:206px;font-size:13px">Deeply Decedant</div>
    <div class="claim" style="left:46px;top:248px">
      <div class="pct" style="font-size:18px"><b>100%</b><small style="font-size:8px">INDULGENCE</small></div>
      <div class="craft" style="font-size:9px">Handcrafted<br>to perfection</div>
    </div>
    <div class="flavour" style="left:48px;top:289px;font-size:11px">VANILLA FLAVOUR</div>
    <div class="scoop" role="img" aria-label="Scoop of vanilla ice cream" style="left:166px;top:226px;width:110px;height:78px"></div>
    <div class="size" style="left:158px;top:222px;width:32px;height:32px;font-size:7px">Net.wt.<br>400ml</div>
  </section>

  <!-- Ice lolly wrapper -->
  <section class="label wrapper" style="left:378px;top:552px;width:263px;height:319px;background:var(--magenta)">
    <svg class="bg" viewBox="0 0 263 319" preserveAspectRatio="none" aria-hidden="true">
      <path d="M63 0 L198 0 L198 10 L263 10 L263 35 C258 50 250 50 248 40 C244 25 230 30 220 40 L198 45 L198 215 C150 230 100 230 66 250 L66 40 C50 30 30 40 20 45 C10 50 5 40 0 45 L0 10 L63 10Z" fill="var(--blush)"/>
      <path d="M63 0 L198 0 L198 10 L63 10Z" fill="var(--white)"/>
      <path d="M0 250 C40 230 30 210 66 210 C120 212 170 205 198 212 L198 319 L0 319Z" fill="var(--magenta-deep)" opacity=".8"/>
      <rect x="66" y="268" width="132" height="10" fill="var(--magenta)"/>
    </svg>
    <div class="brand" style="left:70px;top:44px;width:124px;font-size:20px">Tandle k's</div>
    <div class="script" style="left:70px;top:90px;width:124px;font-size:12px">Premium Gelato</div>
    <div class="product" style="left:72px;top:104px;width:120px;font-size:22px">Ice-cream</div>
    <div class="tagline" style="left:70px;top:130px;width:124px;text-align:center;font-size:8px">Deeply Decedant</div>
    <div class="scoop" role="img" aria-label="Scoop of vanilla ice cream" style="left:82px;top:152px;width:100px;height:72px"></div>
    <div class="claim" style="left:92px;top:240px">
      <div class="pct" style="font-size:12px"><b>100%</b><small style="font-size:5.5px">INDULGENCE</small></div>
      <div class="craft" style="font-size:6px">Handcrafted<br>to perfection</div>
    </div>
    <div class="flavour" style="left:94px;top:270px;font-size:6.5px">VANILLA FLAVOUR</div>
    <div class="size" style="left:164px;top:266px;width:14px;height:14px;font-size:3px;border-width:1px">Made<br>in UK</div>
  </section>

  <!-- 10 litre tub lid sticker -->
  <section class="label lid" style="left:675px;top:552px;width:320px;height:319px">
    <svg class="bg" viewBox="0 0 320 319" preserveAspectRatio="none" aria-hidden="true">
      <path d="M0 45 C20 35 40 40 55 55 C65 70 80 40 105 35 L240 30 C255 28 270 40 280 55 C285 65 295 50 305 35 C310 30 316 32 320 38 L320 319 L0 319Z" fill="var(--blush)"/>
      <path d="M0 245 C80 225 170 232 240 228 C270 226 300 218 320 214 L320 319 L0 319Z" fill="var(--magenta-deep)"/>
      <rect x="0" y="292" width="320" height="18" fill="var(--magenta)"/>
    </svg>
    <div class="brand" style="left:35px;top:58px;width:260px;font-size:42px">Tandle k's</div>
    <div class="script" style="left:35px;top:132px;width:260px;font-size:22px">Premium Gelato</div>
    <div class="product" style="left:30px;top:158px;width:270px;font-size:46px">Ice-cream</div>
    <div class="tagline" style="left:48px;top:212px;font-size:13px">Deeply Decedant</div>
    <div class="claim" style="left:48px;top:254px">
      <div class="pct" style="font-size:18px"><b>100%</b><small style="font-size:8px">INDULGENCE</small></div>
      <div class="craft" style="font-size:9px">Handcrafted<br>to perfection</div>
    </div>
    <div class="flavour" style="left:49px;top:295px;font-size:11px">VANILLA FLAVOUR</div>
    <div class="scoop" role="img" aria-label="Scoop of vanilla ice cream" style="left:172px;top:230px;width:110px;height:78px"></div>
    <div class="size" style="left:162px;top:226px;width:32px;height:32px;font-size:9px">10ltrs</div>
  </section>

  <!-- 5 litre napoli pan side sticker -->
  <section class="label pan" style="left:171px;top:906px;width:697px;height:255px">
    <svg class="bg" viewBox="0 0 697 255" preserveAspectRatio="none" aria-hidden="true">
      <path d="M0 40 C20 30 50 45 60 70 C70 90 90 50 110 40 C200 25 300 20 370 30 C390 40 395 60 405 55 C420 40 440 30 470 30 L620 30 C640 30 650 60 660 55 C670 40 685 25 697 20 L697 255 L0 255Z" fill="var(--blush)"/>
      <path d="M0 182 C150 170 300 185 420 175 C520 160 600 120 697 110 L697 255 L0 255Z" fill="var(--magenta-deep)"/>
      <rect x="0" y="231" width="697" height="18" fill="var(--magenta)"/>
    </svg>
    <div class="brand" style="left:100px;top:38px;width:220px;font-size:30px">Tandle k's</div>
    <div class="script" style="left:100px;top:84px;width:220px;font-size:22px">Premium Gelato</div>
    <div class="product" style="left:95px;top:108px;width:230px;font-size:46px">Ice-cream</div>
    <div class="tagline" style="left:100px;top:160px;width:220px;text-align:center;font-size:13px">Deeply Decedant</div>
    <div class="claim" style="left:120px;top:196px">
      <div class="pct" style="font-size:19px"><b>100%</b><small style="font-size:8.5px">INDULGENCE</small></div>
      <div class="craft" style="font-size:10px">Handcrafted<br>to perfection</div>
    </div>
    <div class="flavour" style="left:120px;top:234px;font-size:12px">VANILLA FLAVOUR</div>
    <div class="scoop" role="img" aria-label="Scoop of vanilla ice cream" style="left:386px;top:80px;width:212px;height:148px"></div>
    <div class="size" style="left:350px;top:178px;width:40px;height:40px;font-size:11px">5ltrs</div>
  </section>

</main>
</body>
</html>
```